Real Estate Website

Please refer to the attached document. It will be for a real estate agency specialising in commercial and residential sales. looking for Modern and minimalist, Sleek, professional, premium feel

```html
<!DOCTYPE html>
<html lang="en">
<head>
<meta charset="utf-8">
<title>Valen Crest Group – Commercial & Residential Property</title>
<link href="https://fonts.googleapis.com/css2?family=Outfit:wght@300;400;500;600;700&display=swap" rel="stylesheet">
<style>
:root{
  --orange:#f04923;
  --orange-soft:#f26a47;
  --navy:#243841;
  --navy-deep:#1d2f37;
  --ink:#2a2a2a;
  --body:#4a4a4a;
  --grey-bg:#efefef;
  --line:#e6e6e6;
  --white:#ffffff;
}
*{box-sizing:border-box;margin:0;padding:0}
html,body{width:1200px;height:4079px;overflow:hidden}
body{font-family:"Outfit",sans-serif;color:var(--ink);background:var(--white);position:relative}
.abs{position:absolute}
a{color:inherit;text-decoration:none}

/* top bar */
.topbar{left:0;top:0;width:1200px;height:27px;background:var(--navy);color:#fff;font-size:12px}
.topbar .tag{left:80px;top:6px}
.topbar .phone{left:705px;top:0;width:250px;height:27px;background:var(--orange);display:flex;align-items:center;gap:6px;padding-left:48px;clip-path:polygon(6% 0,100% 0,100% 100%,0 100%)}
.topbar .phone b{font-weight:600}
.topbar .social{left:1025px;top:7px;display:flex;gap:11px}
.topbar .social i{width:11px;height:11px;border-radius:50%;background:#fff;display:block}
.logo-notch{left:497px;top:0;width:206px;height:27px;background:#fff;clip-path:polygon(0 0,100% 0,94% 100%,6% 100%)}

/* nav */
.nav{left:0;top:27px;width:1200px;height:63px;background:#fff;font-size:14.5px;font-weight:500}
.nav ul{list-style:none;display:flex;gap:28px;position:absolute;top:24px}
.nav .left{left:80px}
.nav .right{left:747px}
.nav li.active{color:var(--orange)}
.brand{left:510px;top:6px;display:flex;align-items:center;gap:10px;font-size:26px;font-weight:600;color:var(--navy);line-height:1}
.brand .dot{width:22px;height:22px;border-radius:50%;background:var(--orange)}

/* hero */
.hero{left:0;top:90px;width:1200px;height:600px;overflow:hidden}
.hero .photo{inset:0;position:absolute;background:linear-gradient(100deg,#2c4450 0%,#3f5e68 35%,#8a7b5c 62%,#c89350 78%,#6d6a5a 100%)}
.hero .cut{position:absolute;left:0;bottom:0;width:1200px;height:90px}
.hero .pill{left:141px;top:62px;border:1px solid rgba(255,255,255,.6);border-radius:20px;padding:7px 18px;font-size:13px;font-weight:500;color:#fff;background:rgba(255,255,255,.08)}
.hero h1{left:141px;top:110px;color:#fff;font-size:36px;line-height:53px;font-weight:400}
.hero h1 strong{font-weight:600}
.hero h1 u{text-decoration:none;border-bottom:3px solid var(--orange)}
.hero .lead{left:141px;top:286px;border-left:2px solid rgba(255,255,255,.7);padding:4px 0 4px 14px;color:#fff;font-size:14.5px;line-height:24px;width:420px}
.btn{display:inline-flex;align-items:center;gap:8px;background:var(--orange);color:#fff;font-size:14px;border-radius:4px}
.hero .btn{left:141px;top:412px;height:46px;padding:0 24px}
.mouse{left:576px;top:646px;width:48px;height:60px;border-radius:24px;background:#fff;box-shadow:0 4px 12px rgba(0,0,0,.12);display:flex;align-items:center;justify-content:center}
.mouse span{width:16px;height:28px;border:2px solid var(--navy);border-radius:8px;position:relative}
.mouse span:after{content:"";position:absolute;left:5px;top:5px;width:2px;height:6px;background:var(--navy)}

/* about */
.about-frame{left:65px;top:754px;width:502px;height:420px;background:var(--orange)}
.about-line{left:86px;top:780px;width:504px;height:414px;border:1.5px solid var(--orange)}
.about-line2{left:80px;top:774px;width:504px;height:414px;border:1.5px solid var(--orange)}
.about-photo{left:75px;top:764px;width:499px;height:414px;background:linear-gradient(135deg,#8b8c88,#c9c4b9 45%,#5e6f5a 80%,#3d4a3e)}
.eyebrow{color:var(--orange);font-size:17px;font-weight:400;letter-spacing:.3px}
.h2{font-size:35px;font-weight:600;color:var(--navy);letter-spacing:-.3px;line-height:1.1}
.about .eyebrow{left:652px;top:772px}
.about .h2{left:652px;top:796px}
.about .copy{left:652px;top:850px;width:430px;font-size:12.2px;line-height:21.8px;color:var(--body)}
.about .copy p{margin-bottom:10px}
.about .btn{left:652px;top:1125px;height:41px;padding:0 25px;border-radius:22px;font-size:12px}

/* services */
.services{left:0;top:1285px;width:1200px;height:615px;background:var(--grey-bg);overflow:hidden}
.services .eyebrow{left:142px;top:88px}
.services .h2{left:142px;top:112px}
.services .copy{left:142px;top:162px;width:300px;font-size:12.5px;line-height:22px;color:var(--body)}
.services .btn{left:142px;top:342px;height:40px;padding:0 25px;border-radius:22px;font-size:12px}
.services .shape{left:37px;top:563px;width:125px;height:60px;background:#f8f8f8}
.svc-photo{left:540px;top:92px;width:518px;height:360px;background:linear-gradient(120deg,#cfc8bb,#9b8a74 45%,#6a5647 75%,#3f342d)}
.svc-photo2{left:1121px;top:92px;width:90px;height:360px;background:linear-gradient(120deg,#2f4f7a,#6b87a6)}
.svc-card-line{left:430px;top:260px;width:282px;height:262px;border:1.5px solid var(--orange)}
.svc-card{left:424px;top:266px;width:282px;height:257px;background:var(--navy);color:#fff;text-align:center;padding:35px 28px 0}
.svc-card h3{font-size:17px;font-weight:600;line-height:24px}
.svc-card p{font-size:12px;line-height:22px;margin-top:14px;color:#e6e9ea}
.svc-card .ghost{display:inline-block;margin-top:14px;border:1.5px solid var(--orange);border-radius:22px;padding:10px 26px;font-size:12px}
.pager{left:807px;top:486px;display:flex;align-items:center;gap:14px;font-size:18px;font-weight:600;color:var(--navy)}
.pager small{font-size:12px;font-weight:500}

/* why */
.why .eyebrow{left:0;width:1200px;text-align:center;top:1988px}
.why .h2{left:0;width:1200px;text-align:center;top:2012px}
.why-card{width:216px;height:265px;border:1px solid var(--line);background:#fff;padding:18px 18px}
.why-card svg{width:46px;height:46px}
.why-card h3{font-size:17.5px;font-weight:600;color:var(--navy);line-height:24px;margin-top:12px}
.why-card p{font-size:12px;line-height:21.5px;color:var(--body);margin-top:14px}
.why-card.featured{background:var(--orange);border:none;height:308px;width:228px;padding:40px 22px}
.why-card.featured h3,.why-card.featured p{color:#fff}

/* careers */
.car-top{left:85px;top:2476px;width:819px;height:38px;background:var(--orange)}
.car-left{left:85px;top:2476px;width:43px;height:299px;background:var(--orange)}
.car-photo{left:141px;top:2528px;width:1059px;height:459px;background:linear-gradient(180deg,#8b8fa4 0%,#c9a06e 32%,#3e4a5f 55%,#274054 80%,#1c2d3a 100%)}
.car-bottom{left:348px;top:2997px;width:852px;height:44px;background:var(--orange)}
.careers .eyebrow{left:218px;top:2743px;color:#fff;font-size:17px}
.careers h2{left:218px;top:2776px;color:#fff;font-size:35px;font-weight:600;line-height:43px}
.careers .ghost{left:218px;top:2873px;height:38px;padding:0 22px;border:1.5px solid var(--orange);border-radius:22px;color:#fff;font-size:12px;display:flex;align-items:center}

/* testimonials */
.testi .eyebrow{left:0;width:1200px;text-align:center;top:3130px}
.testi .h2{left:0;width:1200px;text-align:center;top:3163px}
.t-card{top:3221px;width:288px;height:338px;border:1px solid var(--line);background:#fff;padding:26px 23px}
.t-card .quote{display:flex;gap:6px}
.t-card .quote i{width:16px;height:30px;background:var(--orange);transform:skewX(-14deg);display:block}
.t-card p{font-size:12px;line-height:21.5px;color:var(--body);margin-top:22px}
.t-card h4{font-size:17px;font-weight:600;color:var(--navy);margin-top:22px}
.t-card .stars{color:var(--orange);font-size:15px;letter-spacing:3px}
.dots{left:565px;top:3592px;display:flex;gap:8px;align-items:center}
.dots i{width:9px;height:9px;border-radius:50%;background:#cfcfcf;display:block}
.dots i.on{width:17px;height:17px;border:2px solid var(--orange);background:radial-gradient(var(--orange) 45%,#fff 50%)}

/* footer */
.footer{left:0;top:3704px;width:1200px;height:375px;background:var(--navy);color:#fff}
.footer h5{font-size:16px;font-weight:600;letter-spacing:.3px;padding-bottom:8px;position:relative}
.footer h5:after{content:"";position:absolute;left:0;bottom:0;width:34px;height:2px;background:#fff}
.f-links{left:141px;top:56px}
.f-links ul{list-style:none;margin-top:14px;font-size:12px;line-height:24px}
.f-contact{left:375px;top:56px}
.f-contact .row{display:flex;gap:12px;margin-top:16px;font-size:12px;line-height:19px}
.f-contact .row b{font-weight:600;display:block}
.f-contact svg{width:12px;height:14px;flex:none;margin-top:2px}
.f-follow{left:692px;top:56px}
.f-follow .row{display:flex;align-items:center;gap:10px;margin-top:14px;font-size:12px}
.f-follow .row i{width:29px;height:29px;border-radius:50%;border:1.5px solid #fff;display:block}
.f-follow .row i.on{background:var(--orange);border-color:var(--orange)}
.f-follow .row:first-of-type{margin-top:22px}
.copyright{left:0;top:342px;width:1200px;text-align:center;font-size:11px;color:#dfe3e5}
</style>
</head>
<body>

<!-- top bar -->
<div class="abs topbar">
  <span class="abs tag">Discover the Real Value of investments Your Property</span>
  <div class="abs phone">
    <svg width="12" height="12" viewBox="0 0 24 24"><path fill="#fff" d="M6.6 10.8a15.1 15.1 0 0 0 6.6 6.6l2.2-2.2c.3-.3.7-.4 1-.2 1.1.4 2.3.6 3.6.6.6 0 1 .4 1 1V20c0 .6-.4 1-1 1A17 17 0 0 1 3 4c0-.6.4-1 1-1h3.5c.6 0 1 .4 1 1 0 1.3.2 2.5.6 3.6.1.3 0 .7-.2 1z"/></svg>
    Phone No: <b>(03) 5550 1420</b>
  </div>
  <div class="abs social"><i></i><i></i><i></i><i></i></div>
</div>
<div class="abs logo-notch"></div>

<!-- navigation -->
<nav class="abs nav">
  <ul class="left"><li class="active">Home</li><li>Commercial / Industrial</li><li>Residential</li></ul>
  <ul class="right"><li>Business Sales</li><li>About Us</li><li>Info ⌄</li><li>Contact us</li></ul>
</nav>
<div class="abs brand"><span class="dot"></span>Valen Crest</div>

<!-- hero -->
<section class="abs hero">
  <div class="photo" role="img" aria-label="Harbour at sunset with a waterfront landmark and city skyline"></div>
  <svg class="cut" viewBox="0 0 1200 90" preserveAspectRatio="none">
    <polygon points="0,44 600,90 1200,24 1200,90 0,90" fill="#fff"/>
    <polygon points="700,90 1200,12 1200,32 780,90" fill="var(--orange)"/>
  </svg>
  <span class="abs pill">SPECIALISTS IN</span>
  <h1 class="abs"><strong>Commercial &amp; Industrial</strong><br><u>Property Trusted In</u><br>Residential Property</h1>
  <p class="abs lead">Maximising Returns, Protecting Investments, Delivering Expert Property Advisory.</p>
  <a class="abs btn">Book an Appraisal <svg width="12" height="12" viewBox="0 0 12 12"><path d="M2 10 10 2M4 2h6v6" stroke="#fff" stroke-width="1.5" fill="none"/></svg></a>
</section>
<div class="abs mouse"><span></span></div>

<!-- about -->
<section class="about">
  <div class="abs about-line"></div>
  <div class="abs about-line2"></div>
  <div class="abs about-frame"></div>
  <div class="abs about-photo" role="img" aria-label="Three colleagues reviewing a tablet on an apartment balcony, seen from above"></div>
  <span class="abs eyebrow">WHO WE ARE</span>
  <h2 class="abs h2">VALEN CREST GROUP</h2>
  <div class="abs copy">
    <p>At Valen Crest Group, we are recognised as a trusted authority in commercial and residential property management, sales, and leasing. Property owners, investors, and developers turn to us for our proven expertise, discretion, and consistent results.</p>
    <p>Our mission is to set the standard for excellence in property services. Guided by innovation, integrity, and strategic execution, we deliver outcomes that protect assets, maximise returns, and create enduring value for our clients.</p>
    <p>Whether your goal is to manage your investment, increase rental income, lease to the right tenants, or achieve a successful sale, we provide clarity, confidence, &amp; tailored solutions at every stage of the journey.</p>
  </div>
  <a class="abs btn">READ MORE</a>
</section>

<!-- services -->
<section class="abs services">
  <span class="abs eyebrow">WHAT WE OFFER</span>
  <h2 class="abs h2">OUR SERVICES</h2>
  <p class="abs copy">Ut wisi enim ad minim veniam, quis nostrud exerci tation ullamcorper suscipit lobortis nisl ut aliquip ex ea commodo consequat.</p>
  <a class="abs btn">READ MORE</a>
  <div class="abs shape"></div>
  <div class="abs svc-photo" role="img" aria-label="Two agents smiling while reviewing a tablet indoors"></div>
  <div class="abs svc-photo2" role="img" aria-label="Next service photo, hands with documents"></div>
  <div class="abs svc-card-line"></div>
  <div class="abs svc-card">
    <h3>Strategic Marketing<br>&amp; Leasing</h3>
    <p>Positioning your property to attract premium tenants through targeted, multichannel campaigns.</p>
    <span class="ghost">READ MORE</span>
  </div>
  <div class="abs pager">
    <svg width="26" height="8" viewBox="0 0 26 8"><path d="M1 4h25M4 1 1 4l3 3" stroke="#243841" fill="none"/></svg>
    <span>01/<small>05</small></span>
    <svg width="26" height="8" viewBox="0 0 26 8"><path d="M0 4h25M22 1l3 3-3 3" stroke="#243841" fill="none"/></svg>
  </div>
</section>

<!-- why choose us -->
<section class="why">
  <span class="abs eyebrow">UNIQUE VALUE</span>
  <h2 class="abs h2">WHY CHOOSE US</h2>
  <div class="abs why-card" style="left:142px;top:2096px">
    <svg viewBox="0 0 46 46" fill="none" stroke="#f04923" stroke-width="2"><circle cx="23" cy="20" r="14"/><circle cx="23" cy="20" r="6"/><path d="M6 40h34"/></svg>
    <h3>Sector Expertise</h3>
    <p>Deep knowledge across medical, healthcare, franchise, retail, and industrial sectors, enabling tailored strategies for each asset class.</p>
  </div>
  <div class="abs why-card featured" style="left:369px;top:2074px">
    <svg viewBox="0 0 46 46" fill="none" stroke="#fff" stroke-width="2"><circle cx="23" cy="24" r="14"/><path d="M23 4v6M23 16v16M19 20h8"/></svg>
    <h3>Proactive Asset Management</h3>
    <p>Beyond operations, we actively enhance value, mitigate risk, and secure the right tenants.</p>
  </div>
  <div class="abs why-card" style="left:608px;top:2096px">
    <svg viewBox="0 0 46 46" fill="none" stroke="#f04923" stroke-width="2"><circle cx="20" cy="16" r="10"/><path d="M14 40V28M26 40V28M14 28h12"/></svg>
    <h3>Bespoke Solutions</h3>
    <p>Every property is unique. We craft customised management and leasing strategies aligned with your objectives and market conditions.</p>
  </div>
  <div class="abs why-card" style="left:841px;top:2096px">
    <svg viewBox="0 0 46 46" fill="none" stroke="#f04923" stroke-width="2"><circle cx="23" cy="17" r="12"/><path d="M17 17l4 4 8-8M16 28l-4 14 11-5 11 5-4-14"/></svg>
    <h3>Professional Excellence</h3>
    <p>Integrity, precision, and industry-leading best practices deliver measurable results and peace of mind for discerning property owners.</p>
  </div>
</section>

<!-- careers -->
<section class="careers">
  <div class="abs car-top"></div>
  <div class="abs car-left"></div>
  <div class="abs car-photo" role="img" aria-label="City skyline and river at dusk"></div>
  <div class="abs car-bottom"></div>
  <span class="abs eyebrow">CAREERS</span>
  <h2 class="abs">BUILD YOUR FUTURE IN COMMERCIAL<br>OR RESIDENTIAL REAL ESTATE</h2>
  <a class="abs ghost">JOIN OUR TEAM</a>
</section>

<!-- testimonials -->
<section class="testi">
  <span class="abs eyebrow">SUCCESS STORIES</span>
  <h2 class="abs h2">WHAT OUR CLIENTS SAY</h2>
  <div class="abs t-card" style="left:141px">
    <div class="quote"><i></i><i></i></div>
    <p>Lorem ipsum dolor sit amet consectetuer adipiscing elit, sed diam nonummy nibh euismod tincidunt ut laoreet dore magna aliquam erat volutpat. Ut wisi enim ad minim veniam, quis nostrud exerci tation ullamcorper suscipit lobortis nisl u aliquip ex ea commodo consequat.</p>
    <h4>Olivia R.</h4><div class="stars">★★★★★</div>
  </div>
  <div class="abs t-card" style="left:455px">
    <div class="quote"><i></i><i></i></div>
    <p>Lorem ipsum dolor sit amet consectetuer adipiscing elit, sed diam nonummy nibh euismod tincidunt ut laoreet dore magna aliquam erat volutpat. Ut wisi enim ad minim veniam, quis nostrud exerci tation ullamcorper suscipit lobortis nisl u aliquip ex ea commodo consequat.</p>
    <h4>Olivia R.</h4><div class="stars">★★★★★</div>
  </div>
  <div class="abs t-card" style="left:769px">
    <div class="quote"><i></i><i></i></div>
    <p>Lorem ipsum dolor sit amet consectetuer adipiscing elit, sed diam nonummy nibh euismod tincidunt ut laoreet dore magna aliquam erat volutpat. Ut wisi enim ad minim veniam, quis nostrud exerci tation ullamcorper suscipit lobortis nisl u aliquip ex ea commodo consequat.</p>
    <h4>Olivia R.</h4><div class="stars">★★★★★</div>
  </div>
  <div class="abs dots"><i></i><i class="on"></i><i></i><i></i></div>
</section>

<!-- footer -->
<footer class="abs footer">
  <div class="abs f-links">
    <h5>QUICK LINKS</h5>
    <ul><li>• Home</li><li>• Commercial/industrial</li><li>• Residential</li><li>• Business Sales</li><li>• About Us</li><li>• Info</li><li>• Contact Us</li></ul>
  </div>
  <div class="abs f-contact">
    <h5>CONTACT DETAILS</h5>
    <div class="row"><svg viewBox="0 0 12 14"><path d="M6 13S1 8 1 5a5 5 0 0 1 10 0c0 3-5 8-5 8z" fill="#fff"/><circle cx="6" cy="5" r="1.8" fill="#243841"/></svg><div><b>ADDRESS</b>Suite 14, Level 2, 80 Harbour Lane<br>Eastwick VIC 3010</div></div>
    <div class="row"><svg viewBox="0 0 24 24"><path fill="#fff" d="M6.6 10.8a15.1 15.1 0 0 0 6.6 6.6l2.2-2.2c.3-.3.7-.4 1-.2 1.1.4 2.3.6 3.6.6.6 0 1 .4 1 1V20c0 .6-.4 1-1 1A17 17 0 0 1 3 4c0-.6.4-1 1-1h3.5c.6 0 1 .4 1 1 0 1.3.2 2.5.6 3.6.1.3 0 .7-.2 1z"/></svg><div><b>PHONE</b>1300 55 01 42</div></div>
    <div class="row"><svg viewBox="0 0 12 14"><rect x="0.5" y="3" width="11" height="8" fill="#fff"/><path d="M.5 3 6 8l5.5-5" stroke="#243841" fill="none"/></svg><div><b>EMAIL</b>hello@valencrestgroup.com.au</div></div>
  </div>
  <div class="abs f-follow">
    <h5>FOLLOW US</h5>
    <div class="row"><i class="on"></i>Friendline</div>
    <div class="row"><i></i>Tubecast</div>
    <div class="row"><i></i>Snapgram</div>
    <div class="row"><i></i>Workline</div>
  </div>
  <p class="abs copyright">© 2026 Valen Crest Group. All Rights Reserved.</p>
</footer>

</body>
</html>
```